Business card for a new cabinet shop company named Veloran Cabinets for high end cabinets

Design a business card, thinking dark rich green with colours to speak of high end luxury ie; cream, gold, black possibly

Mitchell Tarrowby
Director Craftsman
Email: info@veloranjoinery-example.com.au
Instagram : @veloran.cabinets

```html
<!DOCTYPE html>
<html lang="en">
<head>
<meta charset="UTF-8">
<title>Veloran Cabinets – Business Card</title>
<link href="https://fonts.googleapis.com/css2?family=Montserrat:wght@400;700&family=Poppins:wght@400&display=swap" rel="stylesheet">
<style>
  :root {
    --backdrop: #9a9a9a;
    --card-green: #1f3d3d;
    --gold: #c9a964;
    --cream-white: #ffffff;
  }
  * { margin: 0; padding: 0; box-sizing: border-box; }
  html, body {
    width: 1200px;
    height: 1059px;
    overflow: hidden;
    background: var(--backdrop);
  }
  .canvas {
    position: relative;
    width: 1200px;
    height: 1059px;
  }
  .card {
    position: absolute;
    left: 253px;
    width: 700px;
    height: 400px;
    background: var(--card-green);
    border-radius: 28px;
    color: var(--cream-white);
    text-align: center;
  }
  .card--front { top: 86px; }
  .card--back { top: 569px; }

  .wordmark {
    position: absolute;
    left: 0;
    right: 0;
    display: flex;
    align-items: center;
    justify-content: center;
    gap: 16px;
    font-family: 'Poppins', sans-serif;
    font-weight: 400;
    color: var(--gold);
    font-size: 46px;
    letter-spacing: 1px;
  }
  .wordmark__dot {
    width: 22px;
    height: 22px;
    border-radius: 50%;
    background: var(--gold);
    flex: none;
  }
  .card--front .wordmark { top: 168px; transform: translateY(-50%); }
  .card--back .wordmark { top: 200px; transform: translateY(-50%); }

  .contact-name {
    position: absolute;
    top: 215px;
    left: 0; right: 0;
    font-family: 'Montserrat', sans-serif;
    font-weight: 700;
    font-size: 32px;
    color: var(--gold);
  }
  .contact-role {
    position: absolute;
    top: 265px;
    left: 0; right: 0;
    font-family: 'Montserrat', sans-serif;
    font-weight: 400;
    font-size: 19px;
  }
  .contact-line {
    position: absolute;
    left: 0; right: 0;
    display: flex;
    align-items: center;
    justify-content: center;
    gap: 9px;
    font-family: 'Montserrat', sans-serif;
    font-weight: 400;
    font-size: 18.5px;
  }
  .contact-line--email { top: 306px; }
  .contact-line--social { top: 341px; }
  .contact-line__icon { flex: none; }
  .social-marker {
    width: 14px;
    height: 14px;
    border: 2px solid var(--gold);
    border-radius: 50%;
    flex: none;
  }
</style>
</head>
<body>
<main class="canvas">
  <section class="card card--front" aria-label="Business card front">
    <div class="wordmark"><span class="wordmark__dot"></span><span>Veloran Cabinets</span></div>
    <h1 class="contact-name">Mitchell Tarrowby</h1>
    <p class="contact-role">Director Craftsman</p>
    <p class="contact-line contact-line--email">
      <svg class="contact-line__icon" width="19" height="14" viewBox="0 0 19 14" aria-hidden="true">
        <rect x="0" y="0" width="19" height="14" rx="1.5" fill="var(--gold)"/>
        <path d="M1 1.5 L9.5 8 L18 1.5" fill="none" stroke="var(--card-green)" stroke-width="1.8"/>
      </svg>
      <span>info@veloranjoinery-example.com.au</span>
    </p>
    <p class="contact-line contact-line--social">
      <span class="social-marker"></span>
      <span>@veloran.cabinets</span>
    </p>
  </section>

  <section class="card card--back" aria-label="Business card back">
    <div class="wordmark"><span class="wordmark__dot"></span><span>Veloran Cabinets</span></div>
  </section>
</main>
</body>
</html>
```